Construction company business card

One side to be the logo with the company name, The other side I would like: (Tomas verbick) Project manager 41 barrow crescent hallam 52917306224783(03) 9703 2428Info@gudeljgroup.comAnd then maybe a couple dot points saying what we do:Construction (commercial & industrial) Civil construction

Anything else please contact me!
Maybe curved st one edge of the card

Target Market(s)

Older clientele

Industry/Entity Type

Construction Company

Contact Information for Business Card

Read above

Colors
3277b5
1b1b1b
9d9d9d

Requirements
Must have
• Use my logo on one side
Nice to have
• Read above
Should not have
• Read above

```html
<!DOCTYPE html>
<html lang="en">
<head>
<meta charset="utf-8">
<title>Stonevale Construction – Business Card</title>
<link href="https://fonts.googleapis.com/css2?family=Work+Sans:wght@400;500;600&display=swap" rel="stylesheet">
<style>
  :root {
    --bg: #141414;
    --card: #1b1b1b;
    --card-edge: #262626;
    --ink: #e6e6e6;
    --ink-soft: #c4c4c4;
    --mark: #9d9d9d;
    --mark-dim: #6f6f6f;
    --rule: #5a5a5a;
  }
  * { box-sizing: border-box; margin: 0; padding: 0; }
  html, body {
    width: 1200px;
    height: 900px;
    overflow: hidden;
    background: var(--bg);
    font-family: "Work Sans", Arial, sans-serif;
  }
  .stage {
    width: 1200px;
    height: 900px;
    display: flex;
    flex-direction: column;
    align-items: center;
    justify-content: center;
    gap: 44px;
  }
  .card {
    width: 665px;
    height: 380px;
    background: var(--card);
    border: 1px solid var(--card-edge);
    position: relative;
  }
  .brand {
    display: flex;
    align-items: center;
    gap: 14px;
    color: var(--mark);
    font-weight: 600;
  }
  .brand-dot {
    width: 46px;
    height: 46px;
    border-radius: 50%;
    border: 5px solid var(--mark);
    flex: none;
  }
  .brand-name {
    display: flex;
    flex-direction: column;
    line-height: 1;
    text-transform: uppercase;
  }
  .brand-name .word { font-size: 34px; letter-spacing: 1px; }
  .brand-name .sub { font-size: 13px; letter-spacing: 6.5px; margin-top: 6px; }

  .card-front {
    display: flex;
    align-items: center;
    justify-content: center;
  }

  .card-back {
    display: flex;
    align-items: center;
    padding: 0 40px 0 50px;
  }
  .card-back .brand { width: 290px; color: var(--mark-dim); }
  .card-back .brand-dot { border-color: var(--mark-dim); }
  .divider {
    width: 1px;
    height: 200px;
    background: var(--rule);
    margin: 0 38px 0 24px;
  }
  .contact { color: var(--ink); }
  .contact .name {
    font-size: 22px;
    font-weight: 500;
    letter-spacing: 1.5px;
    text-transform: uppercase;
  }
  .contact .role {
    font-size: 18px;
    color: var(--ink-soft);
    margin-top: 2px;
  }
  .contact .address {
    font-size: 17px;
    line-height: 1.3;
    margin-top: 12px;
    color: var(--ink-soft);
  }
  .contact .lines { list-style: none; margin-top: 10px; }
  .contact .lines li {
    display: flex;
    align-items: center;
    gap: 8px;
    font-size: 17px;
    line-height: 1.45;
    letter-spacing: 0.5px;
  }
  .contact .lines svg { width: 12px; height: 12px; flex: none; }
</style>
</head>
<body>
<main class="stage">
  <section class="card card-front">
    <div class="brand">
      <span class="brand-dot"></span>
      <span class="brand-name"><span class="word">Stonevale</span><span class="sub">Construction</span></span>
    </div>
  </section>

  <section class="card card-back">
    <div class="brand">
      <span class="brand-dot"></span>
      <span class="brand-name"><span class="word">Stonevale</span><span class="sub">Construction</span></span>
    </div>
    <div class="divider"></div>
    <div class="contact">
      <p class="name">Tomas Verbick</p>
      <p class="role">Project manager</p>
      <p class="address">41 barrow<br>crescent kelmora 5291</p>
      <ul class="lines">
        <li>
          <svg viewBox="0 0 12 12" aria-hidden="true"><path d="M2.5 1 L4.5 1 L5 3.5 L3.8 4.4 C4.4 6 5.9 7.5 7.6 8.2 L8.5 7 L11 7.5 L11 9.5 C11 10.3 10.3 11 9.5 11 C5 10.7 1.3 7 1 2.5 C1 1.7 1.7 1 2.5 1 Z" fill="none" stroke="#e6e6e6" stroke-width="1"/></svg>
          73 0622 4783
        </li>
        <li>
          <svg viewBox="0 0 12 12" aria-hidden="true"><rect x="3" y="0.8" width="6" height="10.4" rx="1" fill="none" stroke="#e6e6e6" stroke-width="1"/><line x1="5" y1="9.3" x2="7" y2="9.3" stroke="#e6e6e6" stroke-width="1"/></svg>
          03 9418 6573
        </li>
        <li>
          <svg viewBox="0 0 12 12" aria-hidden="true"><rect x="0.8" y="2.5" width="10.4" height="7" fill="none" stroke="#e6e6e6" stroke-width="1"/><path d="M0.8 2.5 L6 6.5 L11.2 2.5" fill="none" stroke="#e6e6e6" stroke-width="1"/></svg>
          info@verbickgroup.com
        </li>
      </ul>
    </div>
  </section>
</main>
</body>
</html>
```